TalkHarbor - Language Coaching Services

Sleek, innovative, trendy design for Language Coaching business.

TalkHarbor is a new UK based company that provides Language Coaching services. We offer highly personalized on-line and face to face language courses. We also impart learning techniques workshops based on the latest neuroscience research for second-language acquisition.

Target Market(s)

See attached info

Industry/Entity Type

Consulting

Contact Information for Business Card

TalkHarbor
DaniaKV@talkharbor.co.uk
TalkHarbor.co.uk
London, UK

Font styles to use
Sans Serif

```html
<!DOCTYPE html>
<html lang="en">
<head>
<meta charset="utf-8">
<title>TalkHarbor Business Card</title>
<link rel="stylesheet" href="https://fonts.googleapis.com/css2?family=Open+Sans:wght@400;600;700&display=swap">
<style>
  :root {
    --stage: #1f2023;
    --blue-light: #22b4ec;
    --blue-mid: #0c86c4;
    --blue-deep: #0a5f96;
    --accent-top: #0b6fa8;
    --accent-bottom: #0a5a8e;
    --brand-blue: #1689c4;
    --paper: #ffffff;
    --ink: #3a3a3a;
    --muted: #9a9a9a;
  }
  * { margin: 0; padding: 0; box-sizing: border-box; }
  html, body { width: 1200px; height: 892px; overflow: hidden; }
  body {
    background: var(--stage);
    font-family: "Open Sans", sans-serif;
    position: relative;
  }
  .card {
    position: absolute;
    width: 560px;
    height: 320px;
    overflow: hidden;
  }

  /* Front side */
  .card-front {
    left: 60px;
    top: 90px;
    background: radial-gradient(circle at 50% 45%, var(--blue-light) 0%, var(--blue-mid) 45%, var(--blue-deep) 100%);
    display: flex;
    align-items: center;
    justify-content: center;
    gap: 14px;
  }
  .front-mark {
    width: 26px; height: 26px;
    border: 4px solid var(--paper);
    border-radius: 50%;
  }
  .front-name {
    color: var(--paper);
    font-size: 40px;
    font-weight: 400;
    letter-spacing: 1px;
  }

  /* Back side */
  .card-back {
    left: 580px;
    top: 482px;
    background: var(--paper);
  }
  .back-accent { position: absolute; left: 0; top: 0; }

  .brand {
    position: absolute;
    left: 118px;
    top: 112px;
    display: flex;
    flex-direction: column;
    align-items: center;
    gap: 8px;
  }
  .brand-mark {
    width: 30px; height: 30px;
    border: 4px solid var(--brand-blue);
    border-radius: 50%;
  }
  .brand-name {
    color: var(--brand-blue);
    font-size: 30px;
    font-weight: 400;
    letter-spacing: 1px;
    line-height: 1;
  }

  .person {
    position: absolute;
    right: 28px;
    top: 76px;
    text-align: right;
  }
  .person-name {
    color: var(--brand-blue);
    font-size: 17px;
    font-weight: 700;
    letter-spacing: 0.3px;
    line-height: 22px;
  }
  .person-role {
    color: var(--muted);
    font-size: 11px;
    letter-spacing: 0.5px;
    line-height: 16px;
  }
  .divider { position: absolute; right: 0; top: 126px; }

  .contact {
    position: absolute;
    right: 28px;
    top: 148px;
    list-style: none;
    text-align: right;
  }
  .contact li {
    display: flex;
    align-items: center;
    justify-content: flex-end;
    gap: 8px;
    color: var(--ink);
    font-size: 13px;
    line-height: 20px;
  }
  .contact svg { width: 11px; height: 11px; fill: var(--brand-blue); flex: none; }
</style>
</head>
<body>
  <section class="card card-front" aria-label="Card front">
    <span class="front-mark"></span>
    <span class="front-name">TalkHarbor</span>
  </section>

  <section class="card card-back" aria-label="Card back">
    <svg class="back-accent" width="560" height="320" viewBox="0 0 560 320" aria-hidden="true">
      <polygon points="0,0 40,0 60,190 0,190" fill="var(--accent-top)"/>
      <polygon points="0,190 60,190 120,320 0,320" fill="var(--accent-bottom)"/>
    </svg>

    <div class="brand">
      <span class="brand-mark"></span>
      <span class="brand-name">TalkHarbor</span>
    </div>

    <div class="person">
      <p class="person-name">ELLIS MARLOW</p>
      <p class="person-role">PRESIDENT</p>
    </div>

    <svg class="divider" width="190" height="14" viewBox="0 0 190 14" aria-hidden="true">
      <line x1="14" y1="7" x2="190" y2="7" stroke="#1689c4" stroke-width="2"/>
      <polygon points="0,7 16,1 16,13" fill="#1689c4"/>
    </svg>

    <ul class="contact">
      <li>020 7946 0182
        <svg viewBox="0 0 12 12"><rect x="3" y="0" width="6" height="12" rx="1"/><rect x="4" y="1.5" width="4" height="7" fill="#fff"/></svg>
      </li>
      <li>info@talkharbor.co.uk
        <svg viewBox="0 0 12 12"><rect x="0" y="2" width="12" height="8"/><polyline points="0,2 6,7 12,2" fill="none" stroke="#fff" stroke-width="1"/></svg>
      </li>
      <li>TalkHarbor.co.uk
        <svg viewBox="0 0 12 12"><circle cx="6" cy="6" r="6"/><ellipse cx="6" cy="6" rx="2.5" ry="5.5" fill="none" stroke="#fff" stroke-width="0.8"/><line x1="0.5" y1="6" x2="11.5" y2="6" stroke="#fff" stroke-width="0.8"/></svg>
      </li>
    </ul>
  </section>
</body>
</html>
```